mechanical repair shop

our shop repairs light and medium duty trucks

we sell tires , do oil changes, engine and transmissions
vehicle accessories, alignments, brakes , exhaust, all major and minor repairs.
Updates

if you would like to get a hold of me email: milo.hensworth@quarrytide.net tel: 1-780-555-0148

Target Market(s)

light and medium duty trucks and cars

Industry/Entity Type

Shop

Colors
f37122

Requirements
Must have
• visual sales displays
Nice to have
• pictures

```html
<!DOCTYPE html>
<html lang="en">
<head>
<meta charset="utf-8">
<title>Ridgeline Fleet Services – Truck Repair Flyer</title>
<link href="https://fonts.googleapis.com/css2?family=Oswald:wght@300;400;600&family=Montserrat:wght@400;500&display=swap" rel="stylesheet">
<style>
  :root {
    --orange: #f37122;
    --black: #0c0c0c;
    --ink: #222222;
    --white: #ffffff;
    --backdrop: #3a3a3c;
  }
  * { margin: 0; padding: 0; box-sizing: border-box; }
  html, body {
    width: 1200px; height: 900px; overflow: hidden;
    background: var(--backdrop);
  }
  .flyer {
    position: absolute; left: 300px; top: 26px;
    width: 600px; height: 848px;
    background: var(--white); overflow: hidden;
    font-family: "Montserrat", sans-serif; color: var(--ink);
  }
  .flyer-shapes { position: absolute; inset: 0; }
  .brand {
    position: absolute; right: 30px; top: 34px;
    display: flex; align-items: center; gap: 10px;
  }
  .brand-dot { width: 22px; height: 22px; border-radius: 50%; background: var(--orange); }
  .brand-name {
    font-family: "Oswald", sans-serif; font-weight: 600;
    font-size: 22px; letter-spacing: 1px; color: var(--black);
  }
  .photo { position: absolute; }
  .photo-trucks {
    left: 30px; top: 118px; width: 420px; height: 180px;
    background: linear-gradient(180deg, #f4f4f4 0%, #d9d9d9 60%, #6c6c6c 100%);
    border-radius: 4px;
  }
  .photo-round {
    border-radius: 50%; border: 6px solid var(--orange);
    background: radial-gradient(circle at 40% 40%, #8c8c8c, #2b2b2b 75%);
  }
  .photo-tire { left: 42px; top: 330px; width: 180px; height: 180px; }
  .photo-oil {
    left: 272px; top: 732px; width: 116px; height: 116px;
    background: radial-gradient(circle at 45% 40%, #d9a93a, #6f6a60 45%, #2d2d2d 80%);
  }
  .headline {
    position: absolute; left: 250px; top: 262px; width: 330px;
    font-family: "Oswald", sans-serif; font-weight: 600;
    font-size: 23px; line-height: 1.05; text-transform: uppercase;
    color: var(--white); letter-spacing: -0.3px;
  }
  .headline .accent { color: var(--orange); }
  .services { position: absolute; left: 318px; top: 420px; width: 270px; }
  .services-title {
    font-family: "Oswald", sans-serif; font-weight: 400;
    font-size: 28px; color: var(--orange); margin-bottom: 8px;
  }
  .services-list { list-style: none; }
  .services-list li {
    display: flex; align-items: center; gap: 7px;
    font-size: 10.5px; line-height: 19px; color: var(--ink);
  }
  .tick { width: 10px; height: 10px; flex: none; }
  .about {
    position: absolute; left: 30px; top: 540px; width: 262px;
    font-size: 9.6px; line-height: 1.6; text-align: justify;
  }
  .website {
    position: absolute; left: 30px; top: 818px;
    font-family: "Oswald", sans-serif; font-weight: 300;
    font-size: 13px; color: var(--white); letter-spacing: .3px;
  }
  .contact { position: absolute; right: 28px; top: 778px; text-align: right; }
  .contact-label {
    font-family: "Oswald", sans-serif; font-weight: 400;
    font-size: 15px; color: var(--orange);
  }
  .contact-phone {
    display: flex; align-items: center; justify-content: flex-end; gap: 8px;
    font-family: "Oswald", sans-serif; font-weight: 300;
    font-size: 30px; color: var(--white); line-height: 1.1;
  }
  .contact-phone svg { width: 22px; height: 22px; }
</style>
</head>
<body>
<article class="flyer">
  <svg class="flyer-shapes" viewBox="0 0 600 848" aria-hidden="true">
    <path d="M0,0 H250 C285,110 420,165 600,150 V350 C470,340 330,372 0,468 Z" fill="var(--black)"/>
    <path d="M330,178 C440,178 520,160 600,128 V142 C520,168 440,184 330,178 Z" fill="var(--orange)"/>
    <path d="M210,420 C330,380 470,350 600,350 V360 C470,360 330,392 210,430 Z" fill="var(--orange)"/>
    <path d="M0,800 C180,770 420,800 600,660 V848 H0 Z" fill="var(--black)"/>
    <path d="M0,760 C160,750 260,790 330,790 C250,790 140,775 0,782 Z" fill="var(--orange)"/>
  </svg>

  <div class="brand">
    <span class="brand-dot"></span>
    <span class="brand-name">RIDGELINE</span>
  </div>

  <div class="photo photo-trucks" role="img" aria-label="Photo of three white light and medium duty box trucks"></div>

  <h1 class="headline">Your complete <span class="accent">light medium duty truck</span> repair facility</h1>

  <div class="photo photo-round photo-tire" role="img" aria-label="Photo of a mechanic mounting a truck tire"></div>

  <section class="services">
    <h2 class="services-title">Services We Offer:</h2>
    <ul class="services-list">
      <li><svg class="tick" viewBox="0 0 10 10"><circle cx="5" cy="5" r="4.2" fill="none" stroke="var(--orange)" stroke-width="1.2"/><path d="M3,5 L4.5,6.5 L7,3.5" fill="none" stroke="var(--orange)" stroke-width="1.2"/></svg>Factory recommended service/maintenance</li>
      <li><svg class="tick" viewBox="0 0 10 10"><circle cx="5" cy="5" r="4.2" fill="none" stroke="var(--orange)" stroke-width="1.2"/><path d="M3,5 L4.5,6.5 L7,3.5" fill="none" stroke="var(--orange)" stroke-width="1.2"/></svg>Oil change</li>
      <li><svg class="tick" viewBox="0 0 10 10"><circle cx="5" cy="5" r="4.2" fill="none" stroke="var(--orange)" stroke-width="1.2"/><path d="M3,5 L4.5,6.5 L7,3.5" fill="none" stroke="var(--orange)" stroke-width="1.2"/></svg>Fuel system repair and maintenance</li>
      <li><svg class="tick" viewBox="0 0 10 10"><circle cx="5" cy="5" r="4.2" fill="none" stroke="var(--orange)" stroke-width="1.2"/><path d="M3,5 L4.5,6.5 L7,3.5" fill="none" stroke="var(--orange)" stroke-width="1.2"/></svg>Battery system diagnosis &amp; repair</li>
      <li><svg class="tick" viewBox="0 0 10 10"><circle cx="5" cy="5" r="4.2" fill="none" stroke="var(--orange)" stroke-width="1.2"/><path d="M3,5 L4.5,6.5 L7,3.5" fill="none" stroke="var(--orange)" stroke-width="1.2"/></svg>Check engine light</li>
      <li><svg class="tick" viewBox="0 0 10 10"><circle cx="5" cy="5" r="4.2" fill="none" stroke="var(--orange)" stroke-width="1.2"/><path d="M3,5 L4.5,6.5 L7,3.5" fill="none" stroke="var(--orange)" stroke-width="1.2"/></svg>Electrical problems</li>
      <li><svg class="tick" viewBox="0 0 10 10"><circle cx="5" cy="5" r="4.2" fill="none" stroke="var(--orange)" stroke-width="1.2"/><path d="M3,5 L4.5,6.5 L7,3.5" fill="none" stroke="var(--orange)" stroke-width="1.2"/></svg>Engine performance</li>
      <li><svg class="tick" viewBox="0 0 10 10"><circle cx="5" cy="5" r="4.2" fill="none" stroke="var(--orange)" stroke-width="1.2"/><path d="M3,5 L4.5,6.5 L7,3.5" fill="none" stroke="var(--orange)" stroke-width="1.2"/></svg>Exhaust problems</li>
      <li><svg class="tick" viewBox="0 0 10 10"><circle cx="5" cy="5" r="4.2" fill="none" stroke="var(--orange)" stroke-width="1.2"/><path d="M3,5 L4.5,6.5 L7,3.5" fill="none" stroke="var(--orange)" stroke-width="1.2"/></svg>Tires</li>
      <li><svg class="tick" viewBox="0 0 10 10"><circle cx="5" cy="5" r="4.2" fill="none" stroke="var(--orange)" stroke-width="1.2"/><path d="M3,5 L4.5,6.5 L7,3.5" fill="none" stroke="var(--orange)" stroke-width="1.2"/></svg>30/60/90 K mileage maintenance services</li>
      <li><svg class="tick" viewBox="0 0 10 10"><circle cx="5" cy="5" r="4.2" fill="none" stroke="var(--orange)" stroke-width="1.2"/><path d="M3,5 L4.5,6.5 L7,3.5" fill="none" stroke="var(--orange)" stroke-width="1.2"/></svg>Cooling system repair and maintenance</li>
      <li><svg class="tick" viewBox="0 0 10 10"><circle cx="5" cy="5" r="4.2" fill="none" stroke="var(--orange)" stroke-width="1.2"/><path d="M3,5 L4.5,6.5 L7,3.5" fill="none" stroke="var(--orange)" stroke-width="1.2"/></svg>Air conditioning / heating repair</li>
      <li><svg class="tick" viewBox="0 0 10 10"><circle cx="5" cy="5" r="4.2" fill="none" stroke="var(--orange)" stroke-width="1.2"/><path d="M3,5 L4.5,6.5 L7,3.5" fill="none" stroke="var(--orange)" stroke-width="1.2"/></svg>Brake system</li>
      <li><svg class="tick" viewBox="0 0 10 10"><circle cx="5" cy="5" r="4.2" fill="none" stroke="var(--orange)" stroke-width="1.2"/><path d="M3,5 L4.5,6.5 L7,3.5" fill="none" stroke="var(--orange)" stroke-width="1.2"/></svg>Steering &amp; suspension</li>
    </ul>
  </section>

  <p class="about">Ridgeline Fleet Services Ltd. has set up and successfully operates a complete equipment repair facility. First set up to be a dedicated repair shop for a single large client, Ridgeline has now expanded to include all manner of clients with diverse equipment needs. With Journeyman and Apprentice HD mechanics available 24 hours a day our facility is ready to handle all of your equipment needs. We are an ‘approved’ repair facility for a growing list of equipment manufacturers including: Corvane, Tellmark, Brisko, Halvern, Quenlift etc.</p>

  <div class="photo photo-round photo-oil" role="img" aria-label="Photo of engine oil being poured into an engine"></div>

  <p class="website">www.ridgelinefleet.com</p>

  <div class="contact">
    <p class="contact-label">Call us for more information</p>
    <p class="contact-phone">
      <svg viewBox="0 0 24 24" aria-hidden="true"><path d="M6.6 10.8a15.1 15.1 0 0 0 6.6 6.6l2.2-2.2c.3-.3.7-.4 1-.2 1.1.4 2.3.6 3.6.6.6 0 1 .4 1 1V20c0 .6-.4 1-1 1A17 17 0 0 1 3 4c0-.6.4-1 1-1h3.5c.6 0 1 .4 1 1 0 1.3.2 2.5.6 3.6.1.3 0 .7-.2 1z" fill="var(--white)"/></svg>
      780 555 0199
    </p>
  </div>
</article>
</body>
</html>
```